New business card for a regional office of a US M&A company

We need business card for a finance company, office based in Hong Kong , our Head office is in US, our business is to Merge and acquires companies , the new office will be a regional office for the Asia Pacific region. We want to use the head office logo as attached ( but don't have to be exactly the same, can be a variation to it) as a base and then add Asia Pacific alongside the logo.
We would prefer to have be bilingual Eng + Chinese, although we don't really have Chinese company name .

Industry/Entity Type

Business

Contact Information for Business Card

Clara Jo Tsang
 

VP,
APAC M&A Operations
Orin Vantage Asia Pacific Limited
 
Unit 1407, K18
18 Tai Lok Shan Road, 
Hong Kong 
 
M: +852 6038 1742
T : +852 2836 4100
F : +852 2836 4177
VOIP: 4158
 
cjtsang@orinvantage.com

Font styles to use
Serif
Sans Serif

Colors

Designer to choose colors to be used in the design.

Requirements
Must have
• APAC Office

```html
<!DOCTYPE html>
<html lang="en">
<head>
<meta charset="utf-8">
<title>Orin Vantage – APAC Business Card</title>
<link href="https://fonts.googleapis.com/css2?family=Open+Sans:wght@400;600;700;800&display=swap" rel="stylesheet">
<style>
  :root {
    --page-bg: #e6e6e6;
    --card-white: #ffffff;
    --navy: #0c2a44;
    --navy-deep: #091f35;
    --cyan: #22adcb;
    --ink: #3a3f45;
    --ink-soft: #5a5f66;
  }
  * { margin: 0; padding: 0; box-sizing: border-box; }
  html, body { width: 1200px; height: 1000px; overflow: hidden; }
  body {
    background: var(--page-bg);
    font-family: "Open Sans", Arial, sans-serif;
    position: relative;
  }
  .card {
    position: absolute;
    left: 239px;
    width: 698px;
    height: 398px;
    border-radius: 14px;
    overflow: hidden;
  }
  .card--front { top: 82px; background: var(--card-white); }
  .card--back {
    top: 520px;
    background: linear-gradient(160deg, var(--navy) 0%, var(--navy-deep) 100%);
  }
  .wave { position: absolute; left: 0; top: 0; }

  .brand {
    position: absolute;
    display: flex;
    flex-direction: column;
    align-items: center;
  }
  .brand__mark { display: block; }
  .brand__name {
    font-weight: 800;
    color: var(--cyan);
    letter-spacing: 1px;
    white-space: nowrap;
    line-height: 1;
  }
  .card--front .brand { left: 60px; width: 300px; top: 128px; }
  .card--front .brand__mark { width: 56px; height: 56px; background: var(--navy); margin-bottom: 40px; }
  .card--front .brand__name { font-size: 37px; }

  .card--back .brand { left: 0; width: 698px; top: 118px; }
  .card--back .brand__mark { width: 72px; height: 72px; background: var(--card-white); margin-bottom: 50px; }
  .card--back .brand__name { font-size: 48px; }

  .divider {
    position: absolute;
    left: 375px; top: 96px;
    width: 1px; height: 200px;
    background: var(--cyan);
  }
  .person { position: absolute; left: 409px; top: 88px; }
  .person__name { font-size: 24px; font-weight: 400; color: var(--cyan); line-height: 1.2; }
  .person__title { font-size: 15px; font-weight: 600; color: var(--ink); margin-top: 2px; }

  .contacts { position: absolute; left: 409px; top: 159px; list-style: none; }
  .contacts li {
    display: flex; align-items: center;
    height: 20px;
    font-size: 15px; color: var(--ink-soft); letter-spacing: 0.4px;
  }
  .contacts svg { width: 12px; height: 12px; margin-right: 12px; fill: var(--cyan); flex: none; }

  .address {
    position: absolute; left: 409px; top: 252px;
    font-size: 17px; line-height: 22px; color: var(--ink-soft); font-style: normal;
  }
  .voip {
    position: absolute; left: 81px; top: 366px;
    font-size: 15px; color: #ffffff;
  }
</style>
</head>
<body>

<section class="card card--front">
  <svg class="wave" width="698" height="398" viewBox="0 0 698 398">
    <path d="M0 362 C120 330 260 335 420 370 C540 395 620 380 698 368 L698 398 L0 398 Z" fill="var(--cyan)"/>
    <path d="M0 368 C130 342 270 345 420 378 C540 402 620 388 698 373 L698 398 L0 398 Z" fill="#ffffff"/>
    <path d="M0 372 C130 348 270 352 420 384 C540 406 620 392 698 378 L698 398 L0 398 Z" fill="var(--navy)"/>
  </svg>

  <div class="brand">
    <span class="brand__mark"></span>
    <span class="brand__name">ORIN VANTAGE</span>
  </div>

  <div class="divider"></div>

  <div class="person">
    <h1 class="person__name">Clara Jo Tsang</h1>
    <p class="person__title">VP, APAC M&amp;A Operations</p>
  </div>

  <ul class="contacts">
    <li><svg viewBox="0 0 12 12"><path d="M3.5 0h5a1 1 0 0 1 1 1v10a1 1 0 0 1-1 1h-5a1 1 0 0 1-1-1V1a1 1 0 0 1 1-1zm.5 1.5v8h4v-8z"/></svg>+852 6038 1742</li>
    <li><svg viewBox="0 0 12 12"><path d="M2.5 0.5l2 2.5-1 1.3c.6 1.4 1.7 2.5 3.1 3.1l1.3-1 2.6 2-1.3 2.6C5 10.5 1.5 7 .5 2z"/></svg>+852 2836 4100</li>
    <li><svg viewBox="0 0 12 12"><path d="M3 0h6v3H3zM1 4h10v5H9v3H3V9H1zm3 4v3h4V8z"/></svg>+852 2836 4177</li>
    <li><svg viewBox="0 0 12 12"><path d="M0 2h12v1L6 7 0 3zM0 4.5l6 4 6-4V10H0z"/></svg>cjtsang@orinvantage.com</li>
  </ul>

  <address class="address">Unit 1407, K18 18 Tai Lok<br>Shan Road, Hong Kong</address>

  <p class="voip">VOIP: 4158</p>
</section>

<section class="card card--back">
  <div class="brand">
    <span class="brand__mark"></span>
    <span class="brand__name">ORIN VANTAGE</span>
  </div>
</section>

</body>
</html>
```